Employee Benefits Flyer for Recruiting

We are a Steel Product Supplier and Manufacturer in Toledo Ohio.

We would like to create an "attention getting", one-page handout to give prospective employees (both production and administrative) that illustrates all the benefits we offer as a company. An editable document would be preferable as we add more or change existing benefits in the future. Current benefits include:

Individual and Family Medical Insurance
Dental Insurance
Vision Insurance
Short Term Disability Insurance
Critical Illness and Accident Insurance
No Cost Life Insurance Policy
Education Cost Reimbursement
401K with Company Match
Profit Sharing
Attendance and Performance Bonuses
No Cost Legal Assistance
No Cost Counseling Services
No Cost Tobacco Cessation Coaching
No Cost College Planning Assistance
No Cost Work-Life Services
No Cost Employee Discounts
No Cost Legal Consultation
No Cost Financial Consultation
No Cost ID Theft Assistance
No Cost Tax Consultation Assistance
Up to 17 Days of Paid Time Off

Target Market(s)

Potential Employees

Industry/Entity Type

Industrial Manufacturing

Requirements
Must have
• Nicely laid out illustrations / engaging content

```html
<!DOCTYPE html>
<html lang="en">
<head>
<meta charset="utf-8">
<title>Keystone Metal Works – We Are Hiring</title>
<link rel="stylesheet" href="https://fonts.googleapis.com/css2?family=Exo+2:ital,wght@0,800;1,900&family=Montserrat:wght@600;700;800&family=Open+Sans:wght@600;700&display=swap">
<style>
  :root {
    --navy: #0f1b72;
    --navy-deep: #0a1250;
    --blue: #1b55d8;
    --blue-bright: #2a6cf0;
    --orange: #f06a0c;
    --charcoal: #2a2a2a;
    --ink: #1d1d1d;
    --white: #ffffff;
    --page: #eeeeee;
  }
  * { margin: 0; padding: 0; box-sizing: border-box; }
  html, body { width: 783px; height: 1200px; overflow: hidden; background: var(--page); }
  .flyer {
    position: absolute; left: 0; top: 45px;
    width: 783px; height: 1110px;
    background: var(--white);
    box-shadow: 0 4px 18px rgba(0,0,0,.18);
    font-family: "Open Sans", Arial, sans-serif;
    overflow: hidden;
  }
  .flyer-shapes { position: absolute; inset: 0; }
  .abs { position: absolute; }

  .brand { left: 20px; top: 34px; width: 210px; text-align: center; }
  .brand-dot { width: 64px; height: 64px; border-radius: 50%; background: var(--blue); margin: 0 auto 10px; }
  .brand-name { font-family: "Montserrat", sans-serif; font-weight: 800; font-size: 14px; color: var(--blue); letter-spacing: .3px; }

  .headline-top { left: 54px; top: 180px; font-family: "Exo 2", sans-serif; font-weight: 800; font-size: 64px; line-height: 1; color: var(--orange); letter-spacing: 2px; }
  .headline-main {
    left: 50px; top: 242px; font-family: "Exo 2", sans-serif; font-style: italic; font-weight: 900;
    font-size: 92px; line-height: 1; letter-spacing: 2px;
    background: linear-gradient(180deg, #ffffff 0%, #e4e6ea 45%, #9a9ea6 60%, #d8dbe0 100%);
    -webkit-background-clip: text; background-clip: text; color: transparent;
  }
  .headline-rule { left: 80px; top: 344px; width: 86px; height: 5px; background: var(--orange); border-radius: 3px; }
  .headline-sub { left: 49px; top: 366px; font-family: "Montserrat", sans-serif; font-weight: 700; font-size: 27px; color: var(--white); letter-spacing: -.3px; }
  .tagline { left: 49px; top: 421px; font-family: "Open Sans", sans-serif; font-weight: 700; font-size: 16.5px; color: var(--white); letter-spacing: .2px; }

  .benefits-title { left: 48px; top: 464px; font-family: "Montserrat", sans-serif; font-weight: 700; font-size: 27px; color: var(--ink); letter-spacing: .3px; }
  .benefits-title span { color: var(--blue); }
  .benefit-list { left: 58px; top: 505px; list-style: none; }
  .benefit-list li {
    position: relative; padding-left: 22px; height: 23.7px; line-height: 23.7px;
    font-weight: 700; font-size: 15px; color: var(--ink); letter-spacing: .35px; white-space: nowrap;
  }
  .benefit-list li::before {
    content: ""; position: absolute; left: 0; top: 5px; width: 14px; height: 14px; border-radius: 50%;
    background: var(--blue);
  }

  .contact-phone { left: 49px; top: 1031px; display: flex; align-items: center; gap: 8px; font-family: "Open Sans", sans-serif; font-weight: 700; font-size: 25px; color: var(--white); letter-spacing: .5px; }
  .contact-web { left: 49px; top: 1064px; display: flex; align-items: center; gap: 8px; font-weight: 700; font-size: 19px; color: var(--white); letter-spacing: 1.6px; }
  .apply-title { left: 474px; top: 1017px; font-family: "Montserrat", sans-serif; font-weight: 800; font-size: 34px; color: var(--orange); letter-spacing: 1px; line-height: 1; }
  .apply-note { left: 475px; top: 1057px; font-family: "Montserrat", sans-serif; font-weight: 700; font-size: 12px; color: var(--ink); }
  .apply-email { left: 475px; top: 1071px; display: flex; align-items: center; gap: 6px; font-weight: 700; font-size: 15px; color: var(--ink); }
  .icon { display: block; flex: none; }
</style>
</head>
<body>
<main class="flyer">
  <svg class="flyer-shapes" width="783" height="1110" viewBox="0 0 783 1110" aria-hidden="false">
    <defs>
      <linearGradient id="heroBase" x1="0" y1="0" x2="1" y2="0">
        <stop offset="0" stop-color="#101c78"/>
        <stop offset="1" stop-color="#0b1550"/>
      </linearGradient>
      <radialGradient id="welderGlow" cx="0.62" cy="0.55" r="0.6">
        <stop offset="0" stop-color="#e9f2ff"/>
        <stop offset="0.12" stop-color="#5d8ff0"/>
        <stop offset="0.45" stop-color="#1b3aa8"/>
        <stop offset="1" stop-color="#0b1550" stop-opacity="0"/>
      </radialGradient>
      <linearGradient id="panelBlue" x1="0" y1="0" x2="0" y2="1">
        <stop offset="0" stop-color="#1a3fbf"/>
        <stop offset="1" stop-color="#102a96"/>
      </linearGradient>
      <linearGradient id="photoBuilding" x1="0" y1="0" x2="1" y2="1">
        <stop offset="0" stop-color="#9fb7cf"/>
        <stop offset="0.45" stop-color="#2f7dc4"/>
        <stop offset="1" stop-color="#4d6b3a"/>
      </linearGradient>
      <radialGradient id="photoSparks" cx="0.55" cy="0.45" r="0.6">
        <stop offset="0" stop-color="#ffe2b0"/>
        <stop offset="0.2" stop-color="#d8772a"/>
        <stop offset="0.6" stop-color="#3a221a"/>
        <stop offset="1" stop-color="#17120f"/>
      </radialGradient>
      <linearGradient id="photoLathe" x1="0" y1="0" x2="1" y2="0">
        <stop offset="0" stop-color="#1d2a8a"/>
        <stop offset="0.55" stop-color="#2d3570"/>
        <stop offset="0.8" stop-color="#a9adb5"/>
        <stop offset="1" stop-color="#5f636b"/>
      </linearGradient>
    </defs>

    <rect class="hero-bg" x="0" y="0" width="783" height="450" fill="url(#heroBase)"/>
    <g role="img" aria-label="Photo of a welder in a helmet working with bright sparks">
      <rect x="300" y="0" width="483" height="450" fill="url(#welderGlow)"/>
    </g>

    <path class="header-swoosh" d="M0 0 H372 C330 0 315 45 300 90 C285 135 262 158 222 158 H0 Z" fill="var(--blue-bright)"/>
    <path class="header-panel" d="M0 0 H355 C315 0 300 45 286 90 C272 132 250 158 210 158 H0 Z" fill="var(--white)"/>

    <polygon class="tagline-band" points="0,413 633,413 612,450 0,450" fill="var(--orange)"/>
    <rect x="0" y="450" width="783" height="4" fill="var(--white)"/>

    <polygon points="455,463 783,463 783,1009 692,1009" fill="url(#panelBlue)" opacity="0.35"/>
    <rect class="offer-panel" x="692" y="463" width="91" height="546" fill="url(#panelBlue)"/>
    <polygon points="650,636 700,636 690,660 640,660" fill="var(--blue)"/>
    <polygon points="620,810 700,810 690,834 610,834" fill="var(--blue)"/>
    <polygon points="460,986 700,986 692,1009 452,1009" fill="var(--blue)"/>
    <text x="742" y="739" transform="rotate(-90 742 739)" text-anchor="middle" dominant-baseline="middle"
          font-family="Montserrat, sans-serif" font-weight="800" font-size="56" letter-spacing="3"
          fill="#ffffff" fill-opacity="0.18">WE OFFER</text>

    <g class="photo-frame">
      <rect x="438" y="481" width="253" height="160" fill="#ffffff" stroke="#b9bcc2" stroke-width="1.5"/>
      <rect role="img" aria-label="Aerial photo of the company building with a blue roof" x="442" y="485" width="245" height="152" fill="url(#photoBuilding)"/>
    </g>
    <g class="photo-frame">
      <rect x="438" y="655" width="253" height="162" fill="#ffffff" stroke="#b9bcc2" stroke-width="1.5"/>
      <rect role="img" aria-label="Photo of steel plate being cut with a shower of sparks" x="442" y="659" width="245" height="154" fill="url(#photoSparks)"/>
    </g>
    <g class="photo-frame">
      <rect x="438" y="829" width="253" height="161" fill="#ffffff" stroke="#b9bcc2" stroke-width="1.5"/>
      <rect role="img" aria-label="Photo of a metal saw cutting a steel bar" x="442" y="833" width="245" height="153" fill="url(#photoLathe)"/>
    </g>

    <polygon class="contact-band" points="0,1022 449,1022 418,1110 0,1110" fill="var(--charcoal)"/>
  </svg>

  <div class="brand abs">
    <div class="brand-dot"></div>
    <div class="brand-name">KEYSTONE METAL WORKS</div>
  </div>

  <h1 class="headline-top abs">WE ARE</h1>
  <div class="headline-main abs">HIRING</div>
  <div class="headline-rule abs"></div>
  <h2 class="headline-sub abs">PRODUCTION &amp; ADMINISTRATIVE</h2>
  <p class="tagline abs">We are a Steel Product Supplier and Manufacturer in Toledo Ohio</p>

  <h3 class="benefits-title abs">BENEFITS <span>WE OFFER</span></h3>
  <ul class="benefit-list abs">
    <li>Individual and Family Medical Insurance</li>
    <li>Dental Insurance</li>
    <li>Vision Insurance</li>
    <li>Short Term Disability Insurance</li>
    <li>Critical Illness and Accident Insurance</li>
    <li>No Cost Life Insurance Policy</li>
    <li>Education Cost Reimbursement</li>
    <li>401K with Company Match</li>
    <li>Profit Sharing</li>
    <li>Attendance and Performance Bonuses</li>
    <li>No Cost Legal Assistance</li>
    <li>No Cost Counseling Services</li>
    <li>No Cost Tobacco Cessation Coaching</li>
    <li>No Cost College Planning Assistance</li>
    <li>No Cost Work-Life Services</li>
    <li>No Cost Employee Discounts</li>
    <li>No Cost Legal Consultation</li>
    <li>No Cost Financial Consultation</li>
    <li>No Cost ID Theft Assistance</li>
    <li>No Cost Tax Consultation Assistance</li>
    <li>Up to 17 Days of Paid Time Off</li>
  </ul>

  <div class="contact-phone abs">
    <svg class="icon" width="20" height="20" viewBox="0 0 24 24"><path d="M6.6 10.8a15.1 15.1 0 0 0 6.6 6.6l2.2-2.2a1 1 0 0 1 1-.25 11.4 11.4 0 0 0 3.6.57 1 1 0 0 1 1 1V20a1 1 0 0 1-1 1A17 17 0 0 1 3 4a1 1 0 0 1 1-1h3.5a1 1 0 0 1 1 1c0 1.25.2 2.45.57 3.57a1 1 0 0 1-.25 1z" fill="var(--orange)"/></svg>
    <span>419-555-0148</span>
  </div>
  <div class="contact-web abs">
    <svg class="icon" width="18" height="18" viewBox="0 0 24 24" fill="none" stroke="var(--orange)" stroke-width="2"><circle cx="12" cy="12" r="9.5"/><path d="M2.5 12h19M12 2.5c3 3 3 16 0 19M12 2.5c-3 3-3 16 0 19"/></svg>
    <span>www.keystone-metal.com</span>
  </div>

  <div class="apply-title abs">APPLY NOW!</div>
  <div class="apply-note abs">SEND YOUR RESUME AT</div>
  <div class="apply-email abs">
    <svg class="icon" width="17" height="12" viewBox="0 0 17 12"><rect x="0.5" y="0.5" width="16" height="11" fill="var(--orange)"/><path d="M1 1l7.5 6L16 1" fill="none" stroke="#ffffff" stroke-width="1.4"/></svg>
    <span>info@keystone-metal.com</span>
  </div>
</main>
</body>
</html>
```